Corvana Tongue Works, LLC

We need a business card that includes information about our business and conveys a reliable business that provides document translation services and interpreters for a variety of corporate and individual clients. We want to come across as professional, reliable, yet approachable. It should include the following on one side:

ESL / ENL Language Classes, Private Lessons, and Online Tutors
PLEXA Training and Testing
Translating & Interpreting Services
Contact us about Over-the-Phone Interpreting in over 200 languages
24/7/365
www.corvanatongue.example

The other side should include (555) 481-3062

Rhoda Pelling, President
482 Garnet Ave., Ste. 219
Indianapolis, IN 40917

Please add USA as part of the address. Also, please add rmpelling@corvanatongueworks.example as the e-mail address. Thank you.

Target Market(s)

Business professionals, their families, the international community

Industry/Entity Type

Business

Contact Information for Business Card

24/7/365
www.corvanatongue.example

(555) 481-3062

Rhoda Pelling, President
482 Garnet Ave., Ste. 219
Indianapolis, IN 40917
USA

Font styles to use
Sans Serif

Colors

Designer to choose colors to be used in the design.

Requirements
Must have
• See project description
• e-mail address and web address
• Phone number
Nice to have
• a globe
• physical address
Should not have
• Should not have the same color scheme as other agencies in our market in Indiana unless it is blue and black. No purple or yellow.

```html
<!DOCTYPE html>
<html lang="en">
<head>
<meta charset="utf-8">
<title>Corvana Tongue Works — Business Card</title>
<link rel="stylesheet" href="https://fonts.googleapis.com/css2?family=Roboto:wght@400;500;700&display=swap">
<style>
  :root {
    --brand-blue: #2596d6;
    --ink: #111418;
    --paper: #ffffff;
    --banner-grey: #b9b9b9;
    --banner-fold: #7d7d7d;
    --backdrop: #2a2a2a;
    --muted: #3a3a3a;
  }
  * { box-sizing: border-box; margin: 0; padding: 0; }
  html, body {
    width: 1200px; height: 900px; overflow: hidden;
    background: var(--backdrop);
    font-family: "Roboto", Arial, sans-serif;
  }
  .sheet {
    width: 1200px; height: 900px;
    display: flex; flex-direction: column;
    align-items: center; justify-content: center; gap: 40px;
  }
  .card {
    position: relative;
    width: 680px; height: 389px;
    overflow: hidden;
    box-shadow: 0 10px 30px rgba(0,0,0,.5);
  }

  /* Front */
  .card--front { background: var(--brand-blue); }
  .front-brand {
    position: absolute; left: 170px; top: 100px;
    display: flex; align-items: center; gap: 26px;
  }
  .brand-dot {
    width: 150px; height: 150px; border-radius: 50%;
    border: 6px solid var(--paper);
    flex: none;
  }
  .brand-name {
    color: var(--ink); font-weight: 400;
    font-size: 44px; line-height: 1.05;
  }
  .front-web {
    position: absolute; left: 0; right: 0; bottom: 42px;
    text-align: center; color: var(--ink);
    font-size: 17px; letter-spacing: .3px;
  }

  /* Back */
  .card--back { background: var(--paper); }
  .back-shapes { position: absolute; inset: 0; }
  .back-brand {
    position: absolute; left: 40px; top: 120px;
    display: flex; align-items: center; gap: 16px;
  }
  .back-brand .brand-dot {
    width: 96px; height: 96px; border: 4px solid var(--brand-blue);
  }
  .back-brand .brand-name { font-size: 27px; }

  .banner-text {
    position: absolute; left: 350px; top: 42px; width: 260px;
    text-align: center; color: var(--ink);
  }
  .banner-text .person { font-size: 22px; font-weight: 700; }
  .banner-text .role { font-size: 13px; margin-top: 2px; }

  .contact-list {
    position: absolute; left: 40px; top: 262px;
    list-style: none; display: flex; flex-direction: column; gap: 7px;
  }
  .contact-list li {
    display: flex; align-items: center; gap: 12px;
    font-size: 15px; color: var(--ink);
  }
  .contact-icon {
    width: 22px; height: 22px; background: var(--brand-blue);
    display: flex; align-items: center; justify-content: center; flex: none;
  }

  .address {
    position: absolute; left: 430px; top: 222px; width: 230px;
    text-align: center; color: var(--paper);
    font-size: 16px; line-height: 1.35;
  }
  .address svg { display: block; margin: 0 auto 8px; }
</style>
</head>
<body>
<main class="sheet">

  <section class="card card--front" aria-label="Card front">
    <div class="front-brand">
      <span class="brand-dot" aria-hidden="true"></span>
      <p class="brand-name">Corvana<br>Tongue<br>Works, LLC</p>
    </div>
    <p class="front-web">www.corvanatongue.example</p>
  </section>

  <section class="card card--back" aria-label="Card back">
    <svg class="back-shapes" width="680" height="389" viewBox="0 0 680 389" aria-hidden="true">
      <polygon points="330,0 680,0 680,389 430,389" fill="var(--brand-blue)"/>
      <polygon points="300,34 640,34 640,100 300,100" fill="var(--banner-grey)"/>
      <polygon points="300,100 345,100 345,124" fill="var(--banner-fold)"/>
    </svg>

    <div class="banner-text">
      <p class="person">Rhoda Pelling</p>
      <p class="role">President</p>
    </div>

    <div class="back-brand">
      <span class="brand-dot" aria-hidden="true"></span>
      <p class="brand-name">Corvana<br>Tongue<br>Works, LLC</p>
    </div>

    <ul class="contact-list">
      <li>
        <span class="contact-icon"><svg width="14" height="14" viewBox="0 0 24 24"><path fill="#fff" d="M6.6 10.8a15 15 0 0 0 6.6 6.6l2.2-2.2c.3-.3.7-.4 1-.2 1.1.4 2.3.6 3.6.6.6 0 1 .4 1 1V20c0 .6-.4 1-1 1A17 17 0 0 1 3 4c0-.6.4-1 1-1h3.5c.6 0 1 .4 1 1 0 1.3.2 2.5.6 3.6.1.3 0 .7-.2 1z"/></svg></span>
        (555) 481-3062
      </li>
      <li>
        <span class="contact-icon"><svg width="14" height="14" viewBox="0 0 24 24"><rect x="3" y="8" width="18" height="12" rx="2" fill="#fff"/><path d="M2 8c3-4 17-4 20 0" stroke="#fff" stroke-width="2.5" fill="none"/><circle cx="12" cy="14" r="3" fill="var(--brand-blue)"/></svg></span>
        (555) 481-3070
      </li>
      <li>
        <span class="contact-icon"><svg width="14" height="14" viewBox="0 0 24 24"><rect x="2" y="5" width="20" height="14" fill="none" stroke="#fff" stroke-width="2"/><path d="M2 5l10 8 10-8" fill="none" stroke="#fff" stroke-width="2"/></svg></span>
        rmpelling@corvanatongueworks.example
      </li>
      <li>
        <span class="contact-icon"><svg width="14" height="14" viewBox="0 0 24 24"><circle cx="12" cy="12" r="9" fill="none" stroke="#fff" stroke-width="2"/><ellipse cx="12" cy="12" rx="4" ry="9" fill="none" stroke="#fff" stroke-width="2"/><path d="M3 12h18" stroke="#fff" stroke-width="2"/></svg></span>
        www.corvanatongue.example
      </li>
    </ul>

    <address class="address" style="font-style:normal">
      <svg width="14" height="18" viewBox="0 0 24 32" aria-hidden="true"><path fill="#fff" d="M12 0a11 11 0 0 0-11 11c0 8 11 21 11 21s11-13 11-21A11 11 0 0 0 12 0zm0 15a4 4 0 1 1 0-8 4 4 0 0 1 0 8z"/></svg>
      482 Garnet Ave., Ste. 219<br>
      Indianapolis, IN 40917<br>
      USA
    </address>
  </section>

</main>
</body>
</html>
```